Dalvick's Business Card

I need some designs for a new business card including the new logo attached. An old example of our business card is also attached to show all the data that should be included on the new design.
**I added some more examples someone had mocked up**

Contact Information for Business Card

Should include all info on other examples uploaded.

```html
<!DOCTYPE html>
<html lang="en">
<head>
<meta charset="utf-8">
<title>Dalvick's Business Card</title>
<link href="https://fonts.googleapis.com/css2?family=Montserrat:wght@400;500;700&display=swap" rel="stylesheet">
<style>
  :root {
    --page: #ece8e2;
    --card-white: #ffffff;
    --card-dark: #1e1e1e;
    --brand-blue: #1672bd;
    --brand-red: #e3242b;
    --ink: #2a2a2a;
  }
  * { box-sizing: border-box; margin: 0; padding: 0; }
  html, body { width: 900px; height: 1200px; overflow: hidden; }
  body {
    background: var(--page);
    font-family: "Montserrat", Arial, sans-serif;
    position: relative;
  }
  .card {
    position: absolute;
    left: 80px;
    width: 742px;
    height: 440px;
    border-radius: 32px;
    overflow: hidden;
  }
  .card--front { top: 132px; background: var(--card-white); }
  .card--back { top: 638px; background: var(--card-dark); }

  .brand {
    position: absolute;
    display: flex;
    align-items: center;
    gap: 16px;
  }
  .brand__dot {
    width: 58px; height: 58px;
    border-radius: 50%;
    background: var(--brand-red);
    flex: none;
  }
  .brand__name {
    font-weight: 700;
    font-size: 54px;
    letter-spacing: 1px;
    color: var(--brand-blue);
    line-height: 1;
  }
  .card--front .brand { left: 44px; top: 84px; }
  .card--back .brand { left: 50%; top: 50%; transform: translate(-50%, -50%); }
  .card--back .brand__dot { width: 66px; height: 66px; }
  .card--back .brand__name { font-size: 62px; }

  .contact-name {
    position: absolute;
    left: 42px; top: 284px;
    font-weight: 700;
    font-size: 26px;
    color: var(--brand-blue);
  }
  .contact-rule {
    position: absolute;
    left: 42px; top: 321px;
    width: 656px; height: 2px;
    background: var(--brand-blue);
  }
  .contact-list {
    position: absolute;
    left: 42px; top: 336px;
    list-style: none;
    font-size: 16px;
    color: var(--ink);
  }
  .contact-list li { display: flex; align-items: center; gap: 10px; height: 23px; }
  .contact-list svg { width: 16px; height: 14px; flex: none; }
  .credential {
    position: absolute;
    right: 44px; top: 355px;
    font-weight: 500;
    font-size: 15px;
    color: var(--ink);
  }
  .bands { position: absolute; left: 0; top: 0; width: 742px; height: 440px; }
  .tagline {
    position: absolute;
    right: 24px; top: 404px;
    font-weight: 500;
    font-size: 15.5px;
    color: #fff;
  }
  .back-strip {
    position: absolute;
    left: 0; bottom: 0;
    width: 100%; height: 8px;
    background: var(--brand-red);
  }
</style>
</head>
<body>
  <section class="card card--front">
    <svg class="bands" viewBox="0 0 742 440" aria-hidden="true">
      <path d="M0,398 L418,398 C440,398 432,414 410,414 L0,414 Z" fill="var(--brand-red)"/>
      <path d="M0,420 L420,420 C446,420 444,390 478,390 L742,390 L742,440 L0,440 Z" fill="var(--brand-blue)"/>
    </svg>

    <div class="brand">
      <span class="brand__dot"></span>
      <span class="brand__name">DALVICK'S</span>
    </div>

    <h1 class="contact-name">Evan Dalvick</h1>
    <div class="contact-rule"></div>
    <ul class="contact-list">
      <li>
        <svg viewBox="0 0 16 14" aria-hidden="true"><path d="M1,5 C1,1 15,1 15,5 L12,6 L11,4 L5,4 L4,6 Z M3,7 L13,7 L14,13 L2,13 Z" fill="var(--brand-red)"/></svg>
        555.318.4470
      </li>
      <li>
        <svg viewBox="0 0 16 14" aria-hidden="true"><rect x="1" y="2" width="14" height="10" fill="var(--brand-blue)"/><path d="M1,2 L8,8 L15,2" stroke="#fff" stroke-width="1.4" fill="none"/></svg>
        service@dalvickhvac.com
      </li>
    </ul>
    <p class="credential">LICENSED &amp; INSURED</p>
    <p class="tagline">FAMILY OWNED &amp; OPERATED</p>
  </section>

  <section class="card card--back">
    <div class="brand">
      <span class="brand__dot"></span>
      <span class="brand__name">DALVICK'S</span>
    </div>
    <div class="back-strip"></div>
  </section>
</body>
</html>
```